Create a memorable Stationary for Security Software Company

Velbrantix is the worldwide leader in securing the Internet. Making Internet communications and critical data secure, reliable and available everywhere has been and continues to be our ongoing vision. We are committed to staying focused on real customer needs and to developing new and innovative security solutions that redefine the security landscape.

Industry/Entity Type

Internet

Font styles to use
Serif
Sans Serif
Script

Colors
0792cd
33a6d7
85cae6

```html
<!DOCTYPE html>
<html lang="en">
<head>
<meta charset="utf-8">
<title>Velbrantix Business Card</title>
<link rel="stylesheet" href="https://fonts.googleapis.com/css2?family=Source+Sans+3:wght@400;600&display=swap">
<style>
  :root {
    --page-bg: #9a9a9a;
    --sky: #74aed0;
    --band: #2e8cc2;
    --card-back: #2b8bc0;
    --ink-dark: #145a8c;
    --ink-light: #d4e9f5;
    --mark: #5d9fc7;
    --mark-back: #3f97c9;
  }
  * { margin: 0; padding: 0; box-sizing: border-box; }
  html, body { width: 1105px; height: 1200px; overflow: hidden; }
  body {
    background: var(--page-bg);
    font-family: "Source Sans 3", "Myriad Pro", Arial, sans-serif;
    position: relative;
  }
  .card {
    position: absolute;
    left: 182px;
    width: 747px;
    height: 427px;
    overflow: hidden;
  }
  .card-front { top: 119px; background: var(--sky); }
  .card-back { top: 637px; background: var(--card-back); }

  .cloud-band { position: absolute; left: 0; top: 0; width: 747px; height: 427px; }

  .brand {
    position: absolute;
    left: 0; right: 0;
    text-align: center;
  }
  .brand-dot {
    display: block;
    margin: 0 auto 10px;
    border-radius: 50%;
  }
  .card-front .brand { top: 40px; }
  .card-front .brand-dot { width: 86px; height: 86px; background: var(--mark); }
  .card-front .brand-name {
    font-size: 34px; font-weight: 600; color: var(--ink-light); letter-spacing: 0.5px;
  }
  .card-back .brand { top: 120px; }
  .card-back .brand-dot { width: 150px; height: 150px; background: var(--mark-back); }
  .card-back .brand-name {
    font-size: 36px; font-weight: 600; color: var(--ink-dark);
  }

  .person {
    position: absolute;
    left: 46px;
    top: 270px;
    line-height: 1.35;
  }
  .person-name { font-size: 26px; font-weight: 600; color: var(--ink-dark); }
  .person-title { font-size: 21px; color: var(--ink-dark); margin-bottom: 6px; }
  .person-address { font-size: 20px; color: var(--ink-light); line-height: 1.45; }

  .contacts {
    position: absolute;
    right: 40px;
    top: 277px;
    list-style: none;
  }
  .contacts li {
    display: flex;
    justify-content: flex-end;
    align-items: center;
    height: 29px;
    font-size: 20px;
    color: var(--ink-light);
  }
  .contacts svg { width: 18px; height: 18px; margin-left: 16px; fill: var(--ink-dark); }

  .back-web {
    position: absolute;
    left: 0; right: 0;
    top: 352px;
    text-align: center;
    font-size: 19px;
    letter-spacing: 9px;
    color: #1f6a9c;
  }
</style>
</head>
<body>

<section class="card card-front" aria-label="Business card front">
  <svg class="cloud-band" viewBox="0 0 747 427" aria-hidden="true">
    <path fill="var(--band)" d="M0,232 A40,26 0 0 1 62,222 A42,28 0 0 1 138,226 A36,24 0 0 1 196,230 A44,30 0 0 1 268,224 A38,26 0 0 1 332,228 A46,30 0 0 1 410,222 A40,26 0 0 1 476,228 A44,30 0 0 1 548,222 A38,26 0 0 1 612,228 A44,30 0 0 1 686,222 A36,24 0 0 1 747,228 L747,427 L0,427 Z"/>
  </svg>

  <div class="brand">
    <span class="brand-dot"></span>
    <span class="brand-name">Velbrantix</span>
  </div>

  <div class="person">
    <div class="person-name">Elin Varga</div>
    <div class="person-title">CEO/Founder</div>
    <div class="person-address">4812 Larkspur Way<br>Halden Bay, Norland 52810</div>
  </div>

  <ul class="contacts">
    <li>611 204 7795
      <svg viewBox="0 0 24 24"><path d="M6.6 10.8a15.1 15.1 0 0 0 6.6 6.6l2.2-2.2a1 1 0 0 1 1-.25 11.4 11.4 0 0 0 3.6.57 1 1 0 0 1 1 1V20a1 1 0 0 1-1 1A17 17 0 0 1 3 4a1 1 0 0 1 1-1h3.5a1 1 0 0 1 1 1c0 1.25.2 2.45.57 3.57a1 1 0 0 1-.25 1z"/></svg>
    </li>
    <li>611 204 7796
      <svg viewBox="0 0 24 24"><path d="M6 2h12v5H6zM3 8h18a1 1 0 0 1 1 1v8h-4v5H6v-5H2V9a1 1 0 0 1 1-1zm5 8v4h8v-4z"/></svg>
    </li>
    <li>elin@velbrantix.com
      <svg viewBox="0 0 24 24"><path d="M2 5h20v14H2zm2 2v.5l8 5 8-5V7zm0 3v7h16v-7l-8 5z"/></svg>
    </li>
    <li>www.velbrantix.com
      <svg viewBox="0 0 24 24"><path d="M12 2a10 10 0 1 0 0 20 10 10 0 0 0 0-20zm-1 17.9A8 8 0 0 1 4.1 11H7a14 14 0 0 0 4 8.9zM13 4.1a8 8 0 0 1 6.9 6.9H17a14 14 0 0 0-4-6.9zM9 11a12 12 0 0 1 3-7 12 12 0 0 1 3 7zm0 2h6a12 12 0 0 1-3 7 12 12 0 0 1-3-7z"/></svg>
    </li>
  </ul>
</section>

<section class="card card-back" aria-label="Business card back">
  <div class="brand">
    <span class="brand-dot"></span>
    <span class="brand-name">Velbrantix</span>
  </div>
  <div class="back-web">www.velbrantix.com</div>
</section>

</body>
</html>
```